Veldmark Supplies Business Card

Professional business card that stand out to our potential customers. Front and back with clean modern design

Industry/Entity Type

Oil and gas

Contact Information for Business Card

Name, address, website , office phone and cell number

Requirements
Must have
• Editable files for each employee

```html
<!DOCTYPE html>
<html lang="en">
<head>
<meta charset="utf-8">
<title>Veldmark Supplies Business Card</title>
<link href="https://fonts.googleapis.com/css2?family=Poppins:wght@400;600;700&display=swap" rel="stylesheet">
<style>
  :root {
    --page: #2a2a2c;
    --card: #262627;
    --card-back: #1f1f20;
    --red: #e8242b;
    --cyan: #13b3d4;
    --ink: #f2f2f2;
    --muted: #8a8a8c;
    --rule: #6b6b6d;
  }
  * { margin: 0; padding: 0; box-sizing: border-box; }
  html, body { width: 1200px; height: 900px; overflow: hidden; }
  body {
    background: var(--page);
    font-family: "Poppins", sans-serif;
    color: var(--ink);
    position: relative;
  }
  .card {
    position: absolute;
    left: 320px;
    width: 560px;
    height: 320px;
    border-radius: 18px;
    overflow: hidden;
    box-shadow: 0 10px 30px rgba(0,0,0,.45);
  }
  .card--back { top: 90px; background: var(--card-back); }
  .card--front { top: 470px; background: var(--card); }

  .back-mark {
    position: absolute;
    inset: 0;
    display: flex;
    flex-direction: column;
    align-items: center;
    justify-content: center;
    gap: 22px;
  }
  .back-mark__square {
    width: 70px; height: 70px;
    background: #101011;
    border-radius: 6px;
  }
  .back-mark__name {
    font-weight: 700;
    font-size: 34px;
    letter-spacing: 2px;
    text-transform: uppercase;
    color: #5c5c5e;
  }

  .brand {
    position: absolute;
    left: 40px; top: 70px;
    width: 220px;
    display: flex;
    flex-direction: column;
    align-items: center;
    gap: 16px;
  }
  .brand__square {
    width: 64px; height: 64px;
    background: var(--red);
    border-radius: 6px;
  }
  .brand__name {
    font-weight: 700;
    font-size: 22px;
    letter-spacing: 1px;
    text-transform: uppercase;
    color: var(--red);
    text-align: center;
  }
  .divider {
    position: absolute;
    left: 282px; top: 60px;
    width: 1px; height: 170px;
    background: var(--rule);
  }
  .contact {
    position: absolute;
    left: 304px; top: 58px;
    font-size: 12.5px;
    line-height: 1.45;
  }
  .contact__name {
    font-weight: 700;
    font-size: 22px;
    color: var(--red);
    line-height: 1.1;
  }
  .contact__role { font-size: 13px; margin-bottom: 8px; }
  .contact__address { margin-bottom: 6px; }
  .contact__row { display: flex; align-items: center; gap: 8px; }
  .contact__row svg { width: 11px; height: 11px; flex: none; }

  .band {
    position: absolute;
    left: 0; bottom: 0;
    width: 100%; height: 14px;
  }
</style>
</head>
<body>

<section class="card card--back" aria-label="Card back">
  <div class="back-mark">
    <div class="back-mark__square"></div>
    <div class="back-mark__name">Veldmark Supplies</div>
  </div>
</section>

<section class="card card--front" aria-label="Card front">
  <div class="brand">
    <div class="brand__square"></div>
    <div class="brand__name">Veldmark Supplies</div>
  </div>

  <div class="divider"></div>

  <div class="contact">
    <div class="contact__name">Dana Roper</div>
    <div class="contact__role">President</div>
    <div class="contact__address">412 N.Marlow Suite 5<br>Midland, Tx 79701</div>
    <div class="contact__row">
      <svg viewBox="0 0 12 12"><path fill="#e8242b" d="M1 4c0-2 2-3 5-3s5 1 5 3l-2 1-1-2H4L3 5 1 4zM3 6h6l1 5H2z"/></svg>
      <span>(555)014-0382</span>
    </div>
    <div class="contact__row">
      <svg viewBox="0 0 12 12"><rect x="3" y="0.5" width="6" height="11" rx="1" fill="none" stroke="#e8242b" stroke-width="1.2"/><circle cx="6" cy="9.5" r=".8" fill="#e8242b"/></svg>
      <span>(555)014-0382</span>
    </div>
    <div class="contact__row">
      <svg viewBox="0 0 12 12"><rect x="0.5" y="2" width="11" height="8" fill="#e8242b"/><path d="M0.5 2l5.5 4.5L11.5 2" fill="none" stroke="#262627" stroke-width="1"/></svg>
      <span>sales@veldmarksupplies.com</span>
    </div>
    <div class="contact__row">
      <svg viewBox="0 0 12 12"><circle cx="6" cy="6" r="5" fill="none" stroke="#e8242b" stroke-width="1.2"/><path d="M1 6h10M6 1c-2 3-2 7 0 10M6 1c2 3 2 7 0 10" fill="none" stroke="#e8242b" stroke-width=".9"/></svg>
      <span>www.veldmarksupplies.com</span>
    </div>
  </div>

  <svg class="band" viewBox="0 0 560 14" preserveAspectRatio="none" aria-hidden="true">
    <polygon points="0,0 290,0 280,14 0,14" fill="#e8242b"/>
    <polygon points="292,0 560,0 560,14 282,14" fill="#13b3d4"/>
  </svg>
</section>

</body>
</html>
```